Mavel Orquin
Incorporated
Mavel Orquin -
Creative Brief
Use specific fonts
Please use font that would fulfill the requirements of the comment description below
Professional
Derek Holloway
Operations Manager
City of Brenfield, CA
mavelorquin@lumetrix-mail.net
Our company extracts essential and fragrance oil from flowers. We blend our own brand-name perfume and fragrances. Please design cards to reflect a corporate appeal, with feminine luxury, higher end sophistication, yet gentle and soft. Attached is chosen logo. Feel free to take the abstract symbol and name out of the background if deemed necessary.

```html
<!DOCTYPE html>
<html lang="en">
<head>
<meta charset="utf-8">
<title>Mavel Orquin — Stationery Set</title>
<link rel="stylesheet" href="https://fonts.googleapis.com/css2?family=Cormorant+Garamond:wght@500;600&family=Lato:wght@400&display=swap">
<style>
  :root {
    --stage: #e9e6e1;
    --gold-deep: #8a6a2e;
    --gold: #b8934a;
    --gold-light: #d9bf86;
    --gold-pale: #efe2c0;
    --cream: #f6f0d8;
    --cream-soft: #faf6e8;
    --paper: #ffffff;
    --ink: #6b5a3a;
    --swirl: #f1ece0;
  }
  * { margin: 0; padding: 0; box-sizing: border-box; }
  html, body { width: 1200px; height: 578px; overflow: hidden; }
  body {
    background: var(--stage);
    position: relative;
    font-family: "Lato", sans-serif;
    color: var(--ink);
  }
  .piece { position: absolute; box-shadow: 0 2px 6px rgba(0,0,0,.18); overflow: hidden; }

  .brand { display: flex; flex-direction: column; align-items: center; gap: 6px; }
  .brand-mark { border-radius: 50%; background: var(--gold); }
  .brand-name {
    font-family: "Cormorant Garamond", serif;
    font-weight: 600;
    letter-spacing: .22em;
    color: var(--gold);
    text-transform: uppercase;
    white-space: nowrap;
  }

  /* Business card front */
  .card-front {
    left: 48px; top: 41px; width: 281px; height: 158px;
    background: linear-gradient(135deg, var(--gold-light) 0%, var(--gold) 45%, var(--gold-deep) 100%);
  }
  .card-front .brand { position: absolute; left: 22px; top: 28px; align-items: flex-start; }
  .card-front .brand-mark { display: none; }
  .card-front .brand-name { color: var(--cream); font-size: 15px; }
  .card-front .person { position: absolute; left: 22px; top: 108px; color: var(--cream); }
  .person-name { font-family: "Cormorant Garamond", serif; font-size: 12px; font-weight: 600; letter-spacing: .05em; }
  .person-title { font-size: 7px; letter-spacing: .08em; margin-top: 2px; }
  .card-front .contact {
    position: absolute; left: 168px; top: 98px;
    font-size: 6.5px; line-height: 11px; color: var(--cream);
    list-style: none;
  }
  .contact li { display: flex; align-items: center; gap: 4px; }
  .contact li::before { content: ""; width: 4px; height: 4px; border-radius: 50%; background: currentColor; }

  /* Business card back */
  .card-back {
    left: 48px; top: 216px; width: 281px; height: 168px;
    background: var(--cream);
  }
  .card-back .brand { position: absolute; left: 0; right: 0; top: 38px; }
  .card-back .brand-mark { width: 30px; height: 30px; }
  .card-back .brand-name { font-size: 12px; }
  .card-back .band {
    position: absolute; left: 0; right: 0; top: 118px; height: 22px;
    background: linear-gradient(180deg, var(--gold-light), var(--gold-deep));
    display: flex; align-items: center; padding-left: 40px;
    font-size: 7px; color: var(--cream); letter-spacing: .05em;
  }

  /* Letterhead */
  .letterhead {
    left: 355px; top: 38px; width: 389px; height: 509px;
    background: var(--paper);
  }
  .letterhead .pattern {
    position: absolute; left: 0; top: 0; right: 0; bottom: 34px;
    background: radial-gradient(circle at 50% 50%, var(--swirl), var(--paper) 75%);
  }
  .letterhead .brand { position: absolute; left: 24px; top: 16px; align-items: flex-start; }
  .letterhead .brand-mark { width: 22px; height: 22px; margin-left: 22px; }
  .letterhead .brand-name { font-size: 10px; }
  .letterhead .footer {
    position: absolute; left: 0; right: 0; bottom: 0; height: 34px;
    border-top: 1px solid var(--gold-light);
  }
  .footer-line { display: flex; justify-content: center; gap: 22px; font-size: 6.5px; padding-top: 10px; }
  .footer-band { position: absolute; left: 0; right: 0; bottom: 0; height: 5px; background: linear-gradient(90deg, var(--gold-deep), var(--gold-light), var(--gold-deep)); }

  /* Envelope front */
  .envelope-front {
    left: 763px; top: 38px; width: 401px; height: 171px;
    background: var(--paper);
  }
  .envelope-front .pattern {
    position: absolute; inset: 0 0 40px 0;
    background: radial-gradient(circle at 30% 40%, var(--swirl), var(--paper) 70%);
  }
  .envelope-front .brand { position: absolute; left: 16px; top: 10px; }
  .envelope-front .brand-mark { width: 22px; height: 22px; }
  .envelope-front .brand-name { font-size: 9px; }
  .envelope-front .footer { position: absolute; left: 0; right: 0; bottom: 0; height: 40px; }
  .envelope-front .footer-line { padding-top: 14px; }

  /* Envelope back */
  .envelope-back {
    left: 768px; top: 235px; width: 396px; height: 173px;
    background: var(--paper);
  }
  .envelope-back svg { position: absolute; inset: 0; }
  .envelope-back .brand-mark {
    position: absolute; left: 183px; top: 20px; width: 30px; height: 30px;
  }
</style>
</head>
<body>

  <section class="piece card-front" aria-label="Business card front">
    <div class="brand"><span class="brand-name">Mavel Orquin</span></div>
    <div class="person">
      <p class="person-name">Derek Holloway</p>
      <p class="person-title">Operations Manager</p>
    </div>
    <ul class="contact">
      <li>(949) 555-0142</li>
      <li>mavelorquin@lumetrix-mail.net</li>
      <li>City of Brenfield, CA</li>
    </ul>
  </section>

  <section class="piece card-back" aria-label="Business card back">
    <div class="brand">
      <span class="brand-mark"></span>
      <span class="brand-name">Mavel Orquin</span>
    </div>
    <div class="band">mavelorquin@lumetrix-mail.net</div>
  </section>

  <section class="piece letterhead" aria-label="Letterhead">
    <div class="pattern" role="img" aria-label="Faint soft swirl pattern across the page"></div>
    <div class="brand">
      <span class="brand-mark"></span>
      <span class="brand-name">Mavel Orquin</span>
    </div>
    <div class="footer">
      <p class="footer-line"><span>City of Brenfield, CA</span><span>(949) 555-0142</span><span>mavelorquin@lumetrix-mail.net</span></p>
      <div class="footer-band"></div>
    </div>
  </section>

  <section class="piece envelope-front" aria-label="Envelope front">
    <div class="pattern" role="img" aria-label="Faint soft swirl pattern"></div>
    <div class="brand">
      <span class="brand-mark"></span>
      <span class="brand-name">Mavel Orquin</span>
    </div>
    <div class="footer">
      <p class="footer-line"><span>City of Brenfield, CA</span><span>(949) 555-0142</span><span>mavelorquin@lumetrix-mail.net</span></p>
      <div class="footer-band"></div>
    </div>
  </section>

  <section class="piece envelope-back" aria-label="Envelope back">
    <svg width="396" height="173" viewBox="0 0 396 173" aria-hidden="true">
      <path d="M0 0 H396 V8 L198 78 L0 8 Z" fill="#f6f0d8"/>
      <path d="M0 8 L198 78 L396 8" fill="none" stroke="#b8934a" stroke-width="2"/>
    </svg>
    <span class="brand-mark"></span>
  </section>

</body>
</html>
```